Fundraising team needing letterhead for sponsorship and donations

I would like a design that relates to our team name Rosy Wheel Squad. We ride in an annual bicycle event that raises money that goes towards cancer research.We already have a team jersey designed which i have attached. The team name we would prefer to be in pink. Our team includes males and females. The logo also needs to relate to bike riding.

Industry/Entity Type

Event

Font styles to use
Sans Serif

```html
<!DOCTYPE html>
<html lang="en">
<head>
<meta charset="utf-8">
<title>Rosy Wheel Squad – Letterhead</title>
<link href="https://fonts.googleapis.com/css2?family=Open+Sans:wght@400;600;700&display=swap" rel="stylesheet">
<style>
  :root {
    --pink-deep: #e0198c;
    --pink-mid: #ec6fb2;
    --pink-soft: #f6bfdc;
    --pink-faint: #fbe6f1;
    --backdrop: #f4f4f4;
    --paper: #ffffff;
  }
  * { margin: 0; padding: 0; box-sizing: border-box; }
  html, body { width: 1200px; height: 1000px; overflow: hidden; }
  body {
    background: var(--backdrop);
    font-family: "Open Sans", Arial, sans-serif;
    position: relative;
  }
  .letterhead {
    position: absolute;
    left: 264px; top: 30px;
    width: 672px; height: 940px;
    background: var(--paper);
    overflow: hidden;
    box-shadow: 0 6px 24px rgba(0,0,0,0.18);
  }
  .header-band {
    position: absolute; left: 0; top: 0;
    width: 672px; height: 240px;
    background: linear-gradient(180deg, #ea6fb0 0%, #f3a9cf 40%, #fbe0ee 75%, #ffffff 100%);
  }
  .splash-art {
    position: absolute; left: 186px; top: 40px;
    width: 300px; height: 150px;
    border-radius: 50%;
    background: radial-gradient(ellipse at center, rgba(224,25,140,0.55) 0%, rgba(236,111,178,0.3) 50%, rgba(236,111,178,0) 75%);
  }
  .brand-bar {
    position: absolute; left: 126px; top: 120px;
    width: 420px; height: 36px;
    background: linear-gradient(90deg, rgba(224,25,140,0) 0%, var(--pink-deep) 18%, var(--pink-deep) 82%, rgba(224,25,140,0) 100%);
    display: flex; align-items: center; justify-content: center; gap: 10px;
  }
  .brand-dot {
    width: 12px; height: 12px; border-radius: 50%;
    background: var(--paper);
  }
  .brand-name {
    font-size: 22px; font-weight: 700; letter-spacing: 2px;
    color: var(--paper);
    text-transform: uppercase;
    line-height: 1;
  }
  .brand-tagline {
    position: absolute; left: 0; right: 0; top: 160px;
    text-align: center;
    font-size: 10px; font-weight: 600;
    color: var(--pink-deep);
  }
  .watermark {
    position: absolute; left: 0; right: 0; top: 420px;
    text-align: center;
    font-size: 46px; font-weight: 700;
    color: var(--pink-faint);
  }
  .footer-rule {
    position: absolute; left: 28px; right: 28px; top: 790px;
    height: 2px; background: var(--pink-deep);
  }
  .footer-left {
    position: absolute; left: 40px; top: 802px;
    color: var(--pink-deep);
  }
  .footer-name { font-size: 10px; font-weight: 700; text-transform: uppercase; }
  .footer-tag { font-size: 8px; letter-spacing: 1px; text-transform: uppercase; color: var(--pink-mid); }
  .footer-org { font-size: 7px; font-weight: 600; margin-top: 6px; }
  .footer-right {
    position: absolute; left: 400px; top: 812px;
    color: var(--pink-deep); font-size: 7px;
  }
  .footer-phone strong { font-size: 10px; font-weight: 700; }
  .footer-web span { margin-left: 10px; }
</style>
</head>
<body>
  <main class="letterhead">
    <div class="header-band" aria-hidden="true"></div>
    <div class="splash-art" role="img" aria-label="Pink paint splash artwork behind the team name"></div>
    <div class="brand-bar">
      <span class="brand-dot"></span>
      <span class="brand-name">Rosy Wheel Squad</span>
    </div>
    <div class="brand-tagline">Fundraising Bike Ride for Cancer Research</div>

    <div class="watermark">Rosy Wheel Squad</div>

    <div class="footer-rule"></div>
    <div class="footer-left">
      <div class="footer-name">Rosy Wheel Squad</div>
      <div class="footer-tag">Fundraising Bike Ride for Cancer Research</div>
      <div class="footer-org">Organized by : Foundation Name and Address</div>
    </div>
    <div class="footer-right">
      <div class="footer-phone">Phone : <strong>0400 555 018</strong></div>
      <div class="footer-web">www.rosywheelsquad.org.au<span>hello@rosywheelsquad.org.au</span></div>
    </div>
  </main>
</body>
</html>
```